Stationery Set for Velmora Company

I need to create full stationery design for my company; Business Cards, Envelops, Letter Heads, Calendar.
In the letter head and Envelops... only contact information and website links.
Our company is a Service Management company with different domains of innovative services including Technology Service Management, Education Services, Outsourcing Management, Events Management.
I need a modern and innovative design specially for the business card. I some transparent designs and I like it, but don't limit your innovation to what I mentioned. Sky is limit for your innovation.

Target Market(s)

Middle East & Africa

Industry/Entity Type

Business Management

Colors
34a7d8
0355a3
85acd3
86cae7
cee9f5
cfdeed
e4daeb
f3f1f8
ecf7fb

Requirements
Must have
• Name, Title, Email, Mobile
Nice to have
• We have multiple locations in USA, KSA, EGY, so I need ideas about how to include all contact details maybe QR / Barcode or something else.
• Please see our locations and contact information: www.brightvelmora.example
Should not have
• Too much text

```html
<!DOCTYPE html>
<html lang="en">
<head>
<meta charset="utf-8">
<title>Velmora Company – Business Card</title>
<link href="https://fonts.googleapis.com/css2?family=Arimo:wght@400;700&family=Tajawal:wght@500&display=swap" rel="stylesheet">
<style>
  :root {
    --bg: #2b2b2b;
    --brand-blue: #3d6db5;
    --brand-blue-dark: #2f5da4;
    --paper: #ffffff;
    --ink: #1e1e1e;
    --muted-line: #d7dbe2;
    --logo-grey: #8e8e8e;
  }
  * { box-sizing: border-box; margin: 0; padding: 0; }
  html, body { width: 1200px; height: 750px; overflow: hidden; }
  body {
    background: var(--bg);
    font-family: "Arimo", Arial, sans-serif;
    display: flex;
    align-items: center;
    justify-content: center;
    gap: 56px;
  }
  .card {
    width: 520px;
    height: 298px;
    position: relative;
    overflow: hidden;
    box-shadow: 0 10px 28px rgba(0,0,0,.45);
  }
  /* Front */
  .card-front {
    background: var(--brand-blue);
    display: flex;
    flex-direction: column;
    align-items: center;
    justify-content: center;
    color: var(--paper);
  }
  .brand-name {
    font-weight: 700;
    font-size: 54px;
    letter-spacing: 1px;
    line-height: 1;
  }
  .brand-rule {
    width: 250px;
    height: 1px;
    background: rgba(255,255,255,.8);
    margin: 12px 0 8px;
  }
  .brand-arabic {
    font-family: "Tajawal", sans-serif;
    font-size: 22px;
    font-weight: 500;
    direction: rtl;
  }
  /* Back */
  .card-back { background: var(--paper); color: var(--ink); }
  .back-logo {
    position: absolute;
    right: 40px;
    top: 22px;
    text-align: right;
  }
  .back-logo .brand-name { font-size: 44px; color: var(--brand-blue); }
  .back-logo .brand-rule { width: 200px; margin: 8px 0 6px auto; background: var(--brand-blue); }
  .back-logo .brand-arabic { font-size: 18px; color: var(--brand-blue); }
  .contact-band {
    position: absolute;
    left: 0; right: 0;
    top: 132px;
    height: 62px;
    background: var(--brand-blue);
    border-top: 4px solid var(--muted-line);
    color: var(--paper);
    padding: 8px 24px;
  }
  .person { font-size: 17px; line-height: 22px; }
  .person .name { font-weight: 700; text-transform: uppercase; }
  .contacts { font-size: 12.5px; line-height: 20px; white-space: nowrap; }
  .contacts b { font-weight: 700; }
  .office {
    position: absolute;
    top: 206px;
    font-size: 12.5px;
    line-height: 16px;
  }
  .office-ksa { left: 24px; }
  .office-us { right: 24px; text-align: right; }
  .phone-icon { width: 13px; height: 13px; vertical-align: -2px; fill: var(--brand-blue-dark); }
</style>
</head>
<body>
  <section class="card card-front" aria-label="Business card front">
    <div class="brand-name">Velmora</div>
    <div class="brand-rule"></div>
    <div class="brand-arabic">شركة فيلمورا</div>
  </section>

  <section class="card card-back" aria-label="Business card back">
    <div class="back-logo">
      <div class="brand-name">Velmora</div>
      <div class="brand-rule"></div>
      <div class="brand-arabic">شركة فيلمورا</div>
    </div>

    <div class="contact-band">
      <div class="person"><span class="name">Samir Haddad</span> &nbsp;-&nbsp; President</div>
      <div class="contacts"><b>P :</b> +1.5550142870 &nbsp;<b>E :</b> info@brightvelmora.example &nbsp;<b>W :</b> www.brightvelmora.example</div>
    </div>

    <address class="office office-ksa" style="font-style:normal">
      Riyadh, Al Nakheel,<br>
      Qasr Al Warda St.<br>
      Nakheel Plaza Buildings<br>
      Block 4C 3rd Floor C12, C14<br>
      <svg class="phone-icon" viewBox="0 0 24 24" aria-hidden="true"><path d="M6.6 10.8a15 15 0 0 0 6.6 6.6l2.2-2.2a1 1 0 0 1 1-.25 11.4 11.4 0 0 0 3.6.57 1 1 0 0 1 1 1V20a1 1 0 0 1-1 1A17 17 0 0 1 3 4a1 1 0 0 1 1-1h3.5a1 1 0 0 1 1 1c0 1.25.2 2.45.57 3.57a1 1 0 0 1-.25 1z"/></svg>
      +966 92000 17 60
    </address>

    <address class="office office-us" style="font-style:normal">
      418 Harbor Crest Lane<br>
      5th Floor Maple Bay<br>
      CA 90210 US<br>
      +1.5550142870
      <svg class="phone-icon" viewBox="0 0 24 24" aria-hidden="true"><path d="M6.6 10.8a15 15 0 0 0 6.6 6.6l2.2-2.2a1 1 0 0 1 1-.25 11.4 11.4 0 0 0 3.6.57 1 1 0 0 1 1 1V20a1 1 0 0 1-1 1A17 17 0 0 1 3 4a1 1 0 0 1 1-1h3.5a1 1 0 0 1 1 1c0 1.25.2 2.45.57 3.57a1 1 0 0 1-.25 1z"/></svg>
    </address>
  </section>
</body>
</html>
```